Dalvick's Business Card

I need some designs for a new business card including the new logo attached. An old example of our business card is also attached to show all the data that should be included on the new design.
**I added some more examples someone had mocked up**

Contact Information for Business Card

Should include all info on other examples uploaded.

```html
<!DOCTYPE html>
<html lang="en">
<head>
<meta charset="UTF-8">
<title>Dalvick's Business Card</title>
<link rel="stylesheet" href="https://fonts.googleapis.com/css2?family=Montserrat:wght@500;600;700;800&family=Open+Sans:wght@400;600&display=swap">
<style>
  :root {
    --stage: #3b3b3b;
    --card: #141414;
    --brand-blue: #1d6fc2;
    --brand-red: #e2262b;
    --text-light: #f2f2f2;
    --divider: #2a5c92;
    --emboss: #262626;
  }
  * { margin: 0; padding: 0; box-sizing: border-box; }
  html, body { width: 1200px; height: 801px; overflow: hidden; }
  body {
    background: var(--stage);
    font-family: "Open Sans", sans-serif;
    position: relative;
  }
  .card {
    position: absolute;
    top: 252px;
    width: 530px;
    height: 297px;
    background: var(--card);
    border-bottom: 4px solid var(--brand-blue);
    color: var(--text-light);
  }
  .card--front { left: 45px; }
  .card--back { left: 625px; }

  /* Front */
  .brand {
    position: absolute;
    left: 46px;
    top: 58px;
    display: flex;
    align-items: center;
    gap: 14px;
  }
  .brand__dot {
    width: 54px; height: 54px;
    border-radius: 50%;
    background: var(--brand-blue);
  }
  .brand__text { display: flex; flex-direction: column; }
  .brand__name {
    font-family: "Montserrat", sans-serif;
    font-weight: 800;
    font-size: 44px;
    line-height: 1;
    color: var(--brand-blue);
    text-transform: uppercase;
    letter-spacing: 0.5px;
  }
  .brand__tagline {
    font-family: "Montserrat", sans-serif;
    font-weight: 600;
    font-size: 10.5px;
    color: var(--brand-red);
    text-transform: uppercase;
    margin-top: 4px;
    letter-spacing: 0.3px;
  }
  .person {
    position: absolute;
    left: 46px;
    top: 150px;
    display: flex;
    align-items: center;
  }
  .person__name {
    font-family: "Montserrat", sans-serif;
    font-weight: 700;
    font-size: 21px;
    color: var(--brand-blue);
    text-transform: uppercase;
    letter-spacing: 0.5px;
  }
  .person__divider {
    width: 2px; height: 42px;
    background: var(--divider);
    margin: 0 16px;
  }
  .contact { list-style: none; font-size: 13.5px; }
  .contact li { display: flex; align-items: center; gap: 7px; line-height: 21px; }
  .contact svg { width: 11px; height: 11px; fill: var(--brand-red); flex: none; }
  .credentials {
    position: absolute;
    left: 46px;
    bottom: 34px;
    font-family: "Montserrat", sans-serif;
    font-weight: 500;
    font-size: 13.5px;
    text-transform: uppercase;
    letter-spacing: 0.3px;
  }
  .credentials__sep { color: var(--brand-red); margin: 0 10px; }

  /* Back */
  .emblem {
    position: absolute;
    left: 50%;
    top: 62px;
    transform: translateX(-50%);
    display: flex;
    align-items: center;
    gap: 10px;
  }
  .emblem__dot {
    width: 30px; height: 30px;
    border-radius: 50%;
    background: var(--emboss);
  }
  .emblem__name {
    font-family: "Montserrat", sans-serif;
    font-weight: 800;
    font-size: 34px;
    color: var(--emboss);
    text-transform: uppercase;
  }
  .service {
    position: absolute;
    left: 24px; right: 24px;
    bottom: 34px;
    text-align: center;
  }
  .service__area { font-size: 14px; margin-bottom: 4px; }
  .service__cta {
    font-family: "Open Sans", sans-serif;
    font-weight: 600;
    font-size: 13.5px;
    text-transform: uppercase;
    white-space: nowrap;
  }
</style>
</head>
<body>
  <section class="card card--front">
    <div class="brand">
      <span class="brand__dot"></span>
      <div class="brand__text">
        <span class="brand__name">Dalvick's</span>
        <span class="brand__tagline">Air Conditioning &amp; Heating Service</span>
      </div>
    </div>
    <div class="person">
      <span class="person__name">Wesley Dalvick</span>
      <span class="person__divider"></span>
      <ul class="contact">
        <li>
          <svg viewBox="0 0 24 24" aria-hidden="true"><path d="M6.6 10.8a15.1 15.1 0 0 0 6.6 6.6l2.2-2.2a1 1 0 0 1 1-.25 11.4 11.4 0 0 0 3.6.57 1 1 0 0 1 1 1V20a1 1 0 0 1-1 1A17 17 0 0 1 3 4a1 1 0 0 1 1-1h3.5a1 1 0 0 1 1 1c0 1.25.2 2.45.57 3.57a1 1 0 0 1-.25 1z"/></svg>
          555.014.2298
        </li>
        <li>
          <svg viewBox="0 0 24 24" aria-hidden="true"><path d="M2 5h20v2l-10 7L2 7z M2 9.5l10 7 10-7V19H2z"/></svg>
          hvacdalvick@mailbox.com
        </li>
      </ul>
    </div>
    <p class="credentials">Licensed &amp; Insured<span class="credentials__sep">•</span>Family Owned &amp; Operated</p>
  </section>

  <section class="card card--back">
    <div class="emblem">
      <span class="emblem__dot"></span>
      <span class="emblem__name">Dalvick's</span>
    </div>
    <div class="service">
      <p class="service__area">Serves Brookvale, IA &amp; Surrounding Areas</p>
      <p class="service__cta">Call today for all your HVAC, Refrigeration &amp; Plumbing Needs</p>
    </div>
  </section>
</body>
</html>
```